Business card design for Virtual Assistance company

I need a business card designed for my virtual assistance company. We are a small company who services primarily C-level executive clients. The card needs to be double sided with the following contact information on the back:
Melissa Thornbury
Owner/CEO
info@rkpadvisory.net
www.rkpadvisory.net
555.302.9817

The front side should just have the company name incorporated: "RKP Advisory" and "virtual assistance"

The card should be simplistic, but eye catching and should speak to high level executives. Our primary focus areas consist of executive assistance and government contracting.

Target Market(s)

CEOs and executives

Contact Information for Business Card

see project description. phone, email, website.

Colors

Designer to choose only greyscale colors for use in the design.

```html
<!DOCTYPE html>
<html lang="en">
<head>
<meta charset="utf-8">
<title>RKP Advisory – Business Card</title>
<link rel="stylesheet" href="https://fonts.googleapis.com/css2?family=EB+Garamond:wght@400;600;700&family=Montserrat:wght@400&display=swap">
<style>
  :root {
    --backdrop: #d8d6d2;
    --card: #1c1c1c;
    --card-edge: #141414;
    --ink-light: #f4f4f4;
    --ink-soft: #e2e2e2;
    --mark-dark: #0c0c0c;
  }
  * { margin: 0; padding: 0; box-sizing: border-box; }
  html, body { width: 900px; height: 1200px; overflow: hidden; }
  body { background: var(--backdrop); position: relative; font-family: "Montserrat", sans-serif; }

  .card {
    position: absolute;
    left: 80px;
    width: 742px;
    height: 442px;
    border-radius: 24px;
    background: var(--card);
    box-shadow: 0 4px 14px rgba(0,0,0,0.35);
    overflow: hidden;
  }
  .card--front { top: 130px; }
  .card--back { top: 638px; }

  .company-name {
    position: absolute;
    left: 33px;
    top: 34px;
    font-family: "EB Garamond", serif;
    font-weight: 600;
    font-size: 52px;
    line-height: 1;
    color: var(--ink-light);
  }
  .person {
    position: absolute;
    right: 52px;
    top: 48px;
    text-align: right;
  }
  .person__name {
    font-family: "EB Garamond", serif;
    font-weight: 700;
    font-size: 27px;
    line-height: 1;
    color: var(--ink-light);
  }
  .person__title {
    margin-top: 6px;
    font-size: 15px;
    color: var(--ink-soft);
  }

  .contact-list {
    position: absolute;
    left: 45px;
    top: 290px;
    list-style: none;
  }
  .contact-list li {
    display: flex;
    align-items: center;
    height: 28px;
    font-size: 16px;
    color: var(--ink-light);
  }
  .contact-list svg { width: 16px; height: 16px; margin-right: 9px; fill: var(--ink-light); }

  .tagline {
    position: absolute;
    left: 45px;
    top: 390px;
    font-family: "EB Garamond", serif;
    font-size: 17px;
    letter-spacing: 0.3px;
    color: var(--ink-soft);
  }

  .brand-mark {
    position: absolute;
    font-family: "EB Garamond", serif;
    font-weight: 400;
    color: var(--mark-dark);
    line-height: 1;
    white-space: nowrap;
  }
  .brand-mark--front { right: 42px; bottom: 38px; font-size: 62px; }
  .brand-mark--back { left: 0; right: 0; top: 170px; text-align: center; font-size: 112px; }
</style>
</head>
<body>
  <section class="card card--front">
    <h1 class="company-name">RKP Advisory</h1>
    <div class="person">
      <p class="person__name">Melissa Thornbury</p>
      <p class="person__title">Owner/CEO</p>
    </div>
    <ul class="contact-list">
      <li>
        <svg viewBox="0 0 24 24" aria-hidden="true"><path d="M6.6 10.8a15.1 15.1 0 0 0 6.6 6.6l2.2-2.2a1 1 0 0 1 1-.25 11.4 11.4 0 0 0 3.6.57 1 1 0 0 1 1 1V20a1 1 0 0 1-1 1A17 17 0 0 1 3 4a1 1 0 0 1 1-1h3.5a1 1 0 0 1 1 1c0 1.25.2 2.45.57 3.6a1 1 0 0 1-.25 1z"/></svg>
        555.302.9817
      </li>
      <li>
        <svg viewBox="0 0 24 24" aria-hidden="true"><path d="M2 5h20v14H2z M2 5l10 7 10-7" fill="var(--ink-light)"/><path d="M2.5 5.5l9.5 6.7 9.5-6.7" fill="none" stroke="#1c1c1c" stroke-width="1.6"/></svg>
        info@rkpadvisory.net
      </li>
      <li>
        <svg viewBox="0 0 24 24" aria-hidden="true"><circle cx="12" cy="12" r="10"/><path d="M2 12h20M12 2c3 3 3 17 0 20M12 2c-3 3-3 17 0 20" fill="none" stroke="#1c1c1c" stroke-width="1.5"/></svg>
        www.rkpadvisory.net
      </li>
    </ul>
    <p class="tagline">VIRTUAL ASSISTANCE</p>
    <p class="brand-mark brand-mark--front">RKP Advisory</p>
  </section>

  <section class="card card--back">
    <p class="brand-mark brand-mark--back">RKP Advisory</p>
  </section>
</body>
</html>
```